Business card for Eyelash extension salon in Beverly Hills,California USA

We need new business card for our salon in Beverly Hills. The salon name is 'Lashvera' . We would like to have...Business name: Lashvera Name of person: will provide later Address 4720 N.Alder Crest Ave Beverly Hills , CA 90210 Phone: will provide later (Text only) Web: www.lashverastudio.example Snapgrid icon, Circlebook icon follow us for seasonal campaign and news @lashverastudiolounge Design should look elegant, high-end, clean, simple, cohesive with my brand. Please refer my brand board. Business name color will be metallic bronzy color. Im thinking grey background or white background. Thanks

Target Market(s)

25-35. Gender neutral. People who are in Entertainment business industry.
This is High-end Eyelash extension salon in Beverly Hills

Industry/Entity Type

Beauty Salon

Contact Information for Business Card

Business name: Lashvera
Name of person: will provide later
Address 4720 N.Alder Crest Ave Beverly Hills , CA 90210
Phone: will provide later (Text only)
Web: www.lashverastudio.example
Snapgrid icon, Circlebook icon
follow us for seasonal campaign and news @lashverastudiolounge

Requirements
Must have
• Beautiful, elegant, clean and simple look but very attractive and modern
Should not have
• We don't like too clutter, too busy designs.

```html
<!DOCTYPE html>
<html lang="en">
<head>
<meta charset="utf-8">
<title>Lashvera Business Card</title>
<link href="https://fonts.googleapis.com/css2?family=Playfair+Display:wght@400;700&display=swap" rel="stylesheet">
<style>
  :root {
    --bg: #e9e7e4;
    --card: #ffffff;
    --bronze: #8a5a37;
    --ink: #3a3533;
    --rule: #d8c7b6;
    --shadow: rgba(40, 30, 25, 0.18);
  }
  * { box-sizing: border-box; margin: 0; padding: 0; }
  html, body {
    width: 1200px; height: 912px; overflow: hidden;
    background: var(--bg);
    font-family: "Playfair Display", Georgia, serif;
    color: var(--ink);
  }
  .stage {
    position: relative; width: 1200px; height: 912px;
    display: flex; flex-direction: column; align-items: center; justify-content: center; gap: 40px;
  }
  .card {
    position: relative; width: 700px; height: 400px;
    background: var(--card); border-radius: 28px;
    box-shadow: 0 10px 30px var(--shadow);
  }
  /* Front */
  .card--front {
    display: flex; flex-direction: column; align-items: center; justify-content: center;
  }
  .brand-name {
    font-family: "Playfair Display", Georgia, serif;
    font-weight: 400; color: var(--bronze);
    font-size: 72px; letter-spacing: 1px; line-height: 1;
  }
  .card--front .brand-name { margin-bottom: 70px; }
  .social-row {
    display: flex; gap: 22px; align-items: center; margin-bottom: 14px;
    font-size: 13px; color: var(--bronze);
  }
  .social-item { display: flex; align-items: center; gap: 6px; }
  .social-dot { width: 10px; height: 10px; background: var(--bronze); border-radius: 2px; }
  .follow-line { font-size: 16px; color: var(--ink); }
  /* Back */
  .card--back { display: flex; align-items: center; }
  .back-logo {
    width: 350px; display: flex; justify-content: center; align-items: center;
  }
  .divider {
    width: 1px; height: 210px; background: var(--rule);
  }
  .contact { padding-left: 30px; }
  .person-name {
    font-weight: 700; font-size: 26px; color: var(--bronze);
    letter-spacing: 0.5px; line-height: 1.1;
  }
  .person-role { font-size: 15px; margin-bottom: 28px; }
  .address { font-size: 15px; line-height: 1.35; margin-bottom: 12px; }
  .contact-list { list-style: none; }
  .contact-list li {
    display: flex; align-items: center; gap: 12px;
    font-size: 15px; line-height: 1.75;
  }
  .contact-list svg { width: 14px; height: 14px; fill: var(--ink); flex: none; }
  .web-domain { color: var(--bronze); }
</style>
</head>
<body>
<main class="stage">
  <section class="card card--front" aria-label="Card front">
    <div class="brand-name">Lashvera</div>
    <div class="social-row">
      <span class="social-item"><span class="social-dot"></span>Circlebook</span>
      <span class="social-item"><span class="social-dot"></span>Snapgrid</span>
    </div>
    <p class="follow-line">Follow us for seasonal campaign and news @lashverastudiolounge</p>
  </section>

  <section class="card card--back" aria-label="Card back">
    <div class="back-logo"><div class="brand-name">Lashvera</div></div>
    <div class="divider"></div>
    <div class="contact">
      <h1 class="person-name">MIRA CASTELL</h1>
      <p class="person-role">Manager</p>
      <p class="address">4720 N.Alder Crest Ave Beverly Hills<br>CA 90210</p>
      <ul class="contact-list">
        <li>
          <svg viewBox="0 0 24 24" aria-hidden="true"><path d="M6.6 10.8a15.1 15.1 0 0 0 6.6 6.6l2.2-2.2a1 1 0 0 1 1-.25 11.4 11.4 0 0 0 3.6.57 1 1 0 0 1 1 1V20a1 1 0 0 1-1 1A17 17 0 0 1 3 4a1 1 0 0 1 1-1h3.5a1 1 0 0 1 1 1c0 1.25.2 2.45.57 3.57a1 1 0 0 1-.25 1z"/></svg>
          310-555-0148
        </li>
        <li>
          <svg viewBox="0 0 24 24" aria-hidden="true"><path d="M2 5h20v14H2z M4 7v.5l8 5 8-5V7l-8 5z" fill-rule="evenodd"/></svg>
          info@lashverastudio.example
        </li>
        <li>
          <svg viewBox="0 0 24 24" aria-hidden="true"><path d="M12 2a10 10 0 1 0 0 20 10 10 0 0 0 0-20zm0 2c.9 0 2.2 1.8 2.7 5H9.3C9.8 5.8 11.1 4 12 4zM4.3 11h3a18 18 0 0 0 0 2h-3a8 8 0 0 1 0-2zm5 0h5.4a16 16 0 0 1 0 2H9.3a16 16 0 0 1 0-2zm7.4 0h3a8 8 0 0 1 0 2h-3a18 18 0 0 0 0-2zM12 20c-.9 0-2.2-1.8-2.7-5h5.4c-.5 3.2-1.8 5-2.7 5z"/></svg>
          <span>www.<span class="web-domain">lashverastudio.example</span></span>
        </li>
      </ul>
    </div>
  </section>
</main>
</body>
</html>
```